Heron Property Inspection business card

I am the principal inspector of Heron Property Inspections. I serve Northern Virginia from Winchester to Arlington.Associate, Federated Guild of Dwelling Examiners (FGDE)Graduate, FGDE Home Inspectors CourseNational Association of Home Inspectors ExamI'd like the business card to look more professional than comical.I pulled the attached picture off the web. I'd like to have something like that or an image of a house as my logo on the cards.

Target Market(s)

Persons who recently purchased a home.

Industry/Entity Type

Business

Contact Information for Business Card

Bob AllenBadger Home Inspections, LLC.4455 River RoadBluemont, Virginia 20135cell: 703-231-6680e-mail: tkmarlow@postvale.net

Font styles to use
Serif
Sans Serif

Requirements
Must have
• I'd like to have a logo, something that identifies me as a home inspector. The attached images are something that I'd like to have incorporated into my business card logo.
Nice to have
• I'd like a sketch of a house and/or a magnifying glass showing a house being inspected. The attached images are used as a suggestion only, I do not own the images.
Should not have
• Gimmicky stuff. I want to appear professional and trustworthy.

```html
<!DOCTYPE html>
<html lang="en">
<head>
<meta charset="utf-8">
<title>Heron Property Inspections – Business Card</title>
<link href="https://fonts.googleapis.com/css2?family=Marcellus&family=Open+Sans:wght@400;600&display=swap" rel="stylesheet">
<style>
  :root {
    --page-bg: #d9d6d2;
    --band-dark: #2b2a2c;
    --band-mid: #3d3c3e;
    --accent-red: #8e1b1f;
    --rule-red: #a3161c;
    --face-light: #f1eee9;
    --face-cool: #e4e9ee;
    --ink: #2a2a2a;
    --ink-soft: #3a3a3a;
    --logo-ink: #4f4c4c;
  }
  html, body {
    margin: 0;
    width: 1200px;
    height: 970px;
    overflow: hidden;
    background: var(--page-bg);
  }
  .card {
    position: absolute;
    left: 100px;
    top: 208px;
    width: 1000px;
    height: 553px;
    background: linear-gradient(100deg, var(--face-light) 0%, var(--face-cool) 45%, #efe9e4 75%, var(--face-cool) 100%);
    box-shadow: 0 12px 30px rgba(0,0,0,0.18);
    overflow: hidden;
  }
  .band {
    position: absolute;
    left: 0;
    width: 100%;
    background: linear-gradient(90deg, var(--band-mid), var(--band-dark) 50%, var(--band-mid));
  }
  .band--top { top: 0; height: 80px; border-bottom: 4px solid var(--rule-red); }
  .band--bottom { bottom: 0; height: 86px; border-top: 4px solid var(--rule-red); }

  .brand {
    position: absolute;
    left: 60px;
    top: 258px;
    width: 390px;
    display: flex;
    align-items: center;
    gap: 14px;
  }
  .brand__mark {
    width: 18px;
    height: 18px;
    background: var(--accent-red);
    flex: none;
  }
  .brand__name {
    font-family: "Marcellus", serif;
    font-weight: 400;
    color: var(--logo-ink);
    font-size: 27px;
    line-height: 1.25;
    margin: 0;
    white-space: nowrap;
  }

  .divider {
    position: absolute;
    left: 482px;
    top: 154px;
    width: 2px;
    height: 243px;
    background: var(--ink-soft);
  }

  .contact {
    position: absolute;
    left: 566px;
    top: 160px;
    font-family: "Open Sans", sans-serif;
    color: var(--ink);
  }
  .contact__name {
    font-size: 45px;
    font-weight: 600;
    margin: 0;
    line-height: 1;
  }
  .contact__role {
    font-size: 21px;
    margin: 4px 0 0;
    color: var(--ink-soft);
  }
  .contact__list {
    list-style: none;
    padding: 0;
    margin: 28px 0 0;
  }
  .contact__item {
    display: flex;
    align-items: flex-start;
    gap: 24px;
    font-size: 27px;
    line-height: 1.02;
    margin-bottom: 10px;
  }
  .contact__icon {
    width: 22px;
    height: 22px;
    flex: none;
    margin-top: 3px;
  }
</style>
</head>
<body>
  <div class="card">
    <div class="band band--top"></div>

    <div class="brand">
      <span class="brand__mark"></span>
      <p class="brand__name">Tim Marlow Heron<br>Property Inspections, LLC</p>
    </div>

    <div class="divider"></div>

    <div class="contact">
      <h1 class="contact__name">Employee name</h1>
      <p class="contact__role">Managing Director</p>
      <ul class="contact__list">
        <li class="contact__item">
          <svg class="contact__icon" viewBox="0 0 22 22" aria-hidden="true">
            <rect width="22" height="22" rx="4" fill="var(--accent-red)"/>
            <rect x="7" y="5" width="8" height="12" rx="1.5" fill="none" stroke="#fff" stroke-width="1.6"/>
          </svg>
          <span>703-555-0192</span>
        </li>
        <li class="contact__item">
          <svg class="contact__icon" viewBox="0 0 22 22" aria-hidden="true">
            <rect width="22" height="22" rx="4" fill="var(--accent-red)"/>
            <rect x="5" y="7" width="12" height="9" fill="none" stroke="#fff" stroke-width="1.5"/>
            <path d="M5 7 L11 12 L17 7" fill="none" stroke="#fff" stroke-width="1.5"/>
          </svg>
          <span>tkmarlow@postvale.net</span>
        </li>
        <li class="contact__item">
          <svg class="contact__icon" viewBox="0 0 22 22" aria-hidden="true">
            <rect width="22" height="22" rx="4" fill="var(--accent-red)"/>
            <path d="M11 18 C7 13 6.5 11 6.5 9.5 A4.5 4.5 0 0 1 15.5 9.5 C15.5 11 15 13 11 18 Z" fill="#fff"/>
            <circle cx="11" cy="9.5" r="1.7" fill="var(--accent-red)"/>
          </svg>
          <span>7182 Quarry Lane Fernhill,<br>Virginia 20148</span>
        </li>
      </ul>
    </div>

    <div class="band band--bottom"></div>
  </div>
</body>
</html>
```